We need a cover designed for our book on parenting. The focus of this book is on the parents, not on the child! We like the idea of this title having a double meaning - insight as in gaining insights into parenting, and "in sight" as in looking inward as parents and how to improve ourselves rather than looking outward to improve our children. We would love for the cover to somehow represent this double meaning. I can upload an excerpt from the book soon over the next few days.

Reason: We are still reviewing the amazing designs! Thank you so much! :)

Target Market(s)

Parents with kids of any age from babies through adult children.

Requirements
Must have
• Title is: Harborlight Parenting
• Subtitle is: Steady Homes, Calmer Hearts Ahead
• Authors names: Lena Marsh, LCSW Oscar Marsh, Ph.D.

```html
<!DOCTYPE html>
<html lang="en">
<head>
<meta charset="utf-8">
<title>Harborlight Parenting – Book Cover</title>
<link href="https://fonts.googleapis.com/css2?family=Montserrat:wght@900&family=Roboto+Condensed:wght@700&family=Roboto:wght@400&family=Open+Sans:wght@700&display=swap" rel="stylesheet">
<style>
  :root {
    --stage: #ececec;
    --cover-yellow: #f2b60c;
    --ink: #1c1a17;
    --skin-light: #f6d2c2;
    --skin-mid: #eab3a0;
    --label-white: #fbfbfa;
  }
  * { box-sizing: border-box; margin: 0; padding: 0; }
  html, body { width: 1200px; height: 1200px; overflow: hidden; }
  body {
    background: var(--stage);
    position: relative;
    font-family: "Roboto", Arial, sans-serif;
    color: var(--ink);
  }
  .cover {
    position: absolute;
    top: 200px;
    width: 520px;
    height: 780px;
    background: var(--cover-yellow);
    box-shadow: 0 14px 30px rgba(0,0,0,0.18);
    overflow: hidden;
  }
  .cover--front { left: 50px; }
  .cover--back { left: 630px; }

  /* Front */
  .front-title {
    position: absolute;
    top: 70px;
    right: 30px;
    text-align: right;
    font-family: "Montserrat", "Arial Black", sans-serif;
    font-weight: 900;
    line-height: 0.95;
    letter-spacing: -1px;
    text-transform: uppercase;
  }
  .front-title .line-1 { display: block; font-size: 60px; }
  .front-title .line-2 { display: block; font-size: 76px; }
  .front-subtitle {
    position: absolute;
    top: 262px;
    right: 32px;
    text-align: right;
    font-family: "Roboto Condensed", "Arial Narrow", sans-serif;
    font-weight: 700;
    font-size: 30px;
    line-height: 1.12;
  }
  .hands-art {
    position: absolute;
    left: 50px;
    top: 380px;
    width: 420px;
    height: 400px;
  }
  .front-authors {
    position: absolute;
    left: 40px;
    right: 30px;
    bottom: 38px;
    font-size: 25px;
    text-align: center;
  }
  .front-authors .amp { font-size: 16px; }

  /* Back */
  .back-hands-art {
    position: absolute;
    left: 0;
    top: 0;
    width: 200px;
    height: 250px;
  }
  .back-title {
    position: absolute;
    top: 140px;
    left: 220px;
    font-family: "Roboto Condensed", "Arial Narrow", sans-serif;
    font-weight: 700;
    font-size: 38px;
    line-height: 1.1;
  }
  .back-blurb {
    position: absolute;
    top: 292px;
    left: 38px;
    right: 38px;
    font-family: "Open Sans", Arial, sans-serif;
    font-weight: 700;
    font-size: 18px;
    line-height: 1.3;
    text-align: justify;
  }
  .back-label {
    position: absolute;
    right: 38px;
    bottom: 28px;
    width: 200px;
    height: 100px;
    background: var(--label-white);
  }
</style>
</head>
<body>
  <section class="cover cover--front">
    <h1 class="front-title">
      <span class="line-1">Harborlight</span>
      <span class="line-2">Parenting</span>
    </h1>
    <p class="front-subtitle">Steady Homes,<br>Calmer Hearts<br>Ahead</p>
    <svg class="hands-art" viewBox="0 0 420 400" role="img" aria-label="Photo of a small child's hand laid over an adult's open hand">
      <defs>
        <radialGradient id="handGlow" cx="50%" cy="55%" r="55%">
          <stop offset="0%" stop-color="var(--skin-light)"/>
          <stop offset="70%" stop-color="var(--skin-mid)"/>
          <stop offset="100%" stop-color="var(--skin-mid)" stop-opacity="0"/>
        </radialGradient>
      </defs>
      <ellipse cx="210" cy="210" rx="205" ry="200" fill="url(#handGlow)"/>
    </svg>
    <p class="front-authors">Lena Marsh, LCSW <span class="amp">&amp;</span> Oscar Marsh, Ph.D</p>
  </section>

  <section class="cover cover--back">
    <svg class="back-hands-art" viewBox="0 0 200 250" role="img" aria-label="Photo of a child's hand over an adult's hand, cropped at the corner">
      <defs>
        <radialGradient id="backHandGlow" cx="30%" cy="40%" r="70%">
          <stop offset="0%" stop-color="var(--skin-light)"/>
          <stop offset="65%" stop-color="var(--skin-mid)"/>
          <stop offset="100%" stop-color="var(--skin-mid)" stop-opacity="0"/>
        </radialGradient>
      </defs>
      <rect width="200" height="250" fill="url(#backHandGlow)"/>
    </svg>
    <h2 class="back-title">Steady Homes,<br>Calmer Hearts<br>Ahead</h2>
    <p class="back-blurb">We need a cover designed for our book on parenting. The focus of this book is on the parents, not on the child! We like the idea of this title having a double meaning - insight as in gaining insights into parenting, and "in sight" as in looking inward as parents and how to improve ourselves rather than looking outward to improve our children. We would love for the cover to somehow represent this double meaning. I can upload an excerpt from the book soon over the next few days.</p>
    <div class="back-label"></div>
  </section>
</body>
</html>
```